Professional Website for Leading Global Private Equity Real Estate Company

The company is a leading global Private Equity Real Estate (PERE). We need a homepage design, an inner page design, and color/font tweaks to the logo (color should be more soothing than current blue used in the logo). The logo website should project the company as global, professional, experienced, trustworthy, accessible, YOUNG, DYNAMIC, hi-tech. PLEASE SEE the attached Design Brief Word Doc for details.

Target Market(s)

institional investors and wealthy private individuals

Industry/Entity Type

Finance

Number of Pages Required

2 page

Font styles to use
Sans Serif
Other font styles liked:
• either like in https://www.ferndalequay.com/ or like in presentations (Montserrat Black & Montserrat Light, Century Gothic, Blair ITC, Almoni Neue DL 4.0 AAA Medium, Almoni DL AAA)

Requirements
Must have
• new color palette that is NOT based on current logo. they want a more soothing color palette than the blue in that logo. the new color palette should project: global, professional, experienced, trustworthy, accessible, YOUNG, DYNAMIC, hi-tech.
Nice to have
• the likes these sites: https://www.ferndalequay.com/ and https://www.tvr.law/

```html
<!DOCTYPE html>
<html lang="en">
<head>
<meta charset="utf-8">
<title>Alveron Real Estate</title>
<link rel="stylesheet" href="https://fonts.googleapis.com/css2?family=Montserrat:wght@400;500;600;700&family=Roboto:wght@400;500&display=swap">
<style>
:root{
  --teal:#0f4d60;
  --teal-deep:#0b3e4e;
  --teal-btn:#17657b;
  --ink:#2b2f33;
  --body:#3d4246;
  --muted:#6b7074;
  --paper:#f0f0f0;
  --white:#ffffff;
  --rule:#d6d6d6;
}
*{box-sizing:border-box;margin:0;padding:0}
html,body{width:1200px;height:3987px;overflow:hidden}
body{position:relative;background:var(--white);font-family:"Roboto",Arial,sans-serif;color:var(--body)}
.abs{position:absolute}
.heading{font-family:"Montserrat",Arial,sans-serif;font-weight:500;letter-spacing:1px;text-transform:uppercase;color:var(--ink)}
.rule{position:absolute;height:3px;width:58px;background:var(--ink)}
p{font-size:14px;line-height:27px}

/* header */
.site-header{position:absolute;top:0;left:0;width:1200px;height:78px;z-index:3;border-bottom:1px solid rgba(255,255,255,.25)}
.brand{position:absolute;left:100px;top:14px;display:flex;align-items:center;gap:12px;color:var(--white);font-family:"Montserrat",sans-serif;font-weight:500;font-size:19px;letter-spacing:2px;line-height:22px}
.brand-dot{width:48px;height:48px;border-radius:50%;background:var(--white)}
.nav a{position:absolute;top:36px;color:var(--white);font-family:"Roboto",sans-serif;font-size:13px;text-decoration:none;letter-spacing:.3px}
.login{position:absolute;left:1003px;top:25px;width:112px;height:35px;background:var(--teal-btn);color:var(--white);font-size:13px;text-align:center;line-height:35px}

/* hero */
.hero{position:absolute;top:0;left:0;width:1200px;height:706px;background:linear-gradient(180deg,#4b5358 0%,#6b6a62 35%,#6e5a44 70%,#5c4530 100%)}
.hero-shade{position:absolute;inset:0;background:rgba(20,30,35,.28)}
.play{position:absolute;left:583px;top:234px;width:52px;height:52px;border:2px solid #fff;border-radius:50%}
.hero-title{position:absolute;left:0;top:300px;width:1200px;text-align:center;color:var(--white);font-family:"Montserrat",sans-serif;font-weight:500;font-size:40px;line-height:44px;letter-spacing:2px}
.hero-btn{position:absolute;left:526px;top:464px;width:189px;height:47px;border:2px solid #fff;color:#fff;font-family:"Montserrat",sans-serif;font-size:15px;letter-spacing:1.5px;text-align:center;line-height:43px}

/* about */
.about{position:absolute;top:706px;left:0;width:1200px;height:322px;background:var(--paper);overflow:hidden}
.about-circle{position:absolute;left:112px;top:32px;width:276px;height:276px;border-radius:50%;background:var(--white)}
.eyebrow{font-family:"Montserrat",sans-serif;font-size:15px;letter-spacing:1px;text-transform:uppercase}
.stats{position:absolute;top:1028px;left:0;width:1200px;height:116px;background:var(--paper);border-top:1px solid var(--rule)}
.stat{position:absolute;top:0;height:116px}
.stat .value{font-family:"Montserrat",sans-serif;font-weight:600;font-size:34px;color:var(--teal);letter-spacing:1px;margin-top:26px}
.stat .label{font-size:15px;color:var(--ink);letter-spacing:.5px;margin-top:4px;text-transform:uppercase}
.vline{position:absolute;top:1028px;width:1px;height:116px;background:var(--rule)}

/* platforms */
.card{position:absolute;top:1328px;height:287px;overflow:hidden}
.card-photo{position:absolute;inset:0;background:linear-gradient(180deg,#8c8f91,#3e4245)}
.card-label{position:absolute;left:0;width:100%;text-align:center;color:#fff;font-family:"Montserrat",sans-serif;font-weight:600;font-size:13px;letter-spacing:1px;line-height:16px;text-transform:uppercase}
.card-icon{position:absolute;width:50px;height:50px;border-radius:50%;background:var(--teal);display:flex;align-items:center;justify-content:center}
.card-feature{background:var(--teal)}
.card-feature .card-icon{background:transparent;border:2px solid #fff}
.card-copy{position:absolute;left:20px;top:144px;width:200px;text-align:center;color:#d6e3e7;font-size:11.5px;line-height:16px}
.card-more{position:absolute;left:58px;top:227px;width:124px;height:32px;border:2px solid #fff;border-radius:16px;color:#fff;font-size:10px;font-weight:500;text-align:center;line-height:28px;letter-spacing:.5px}

/* edge */
.photo-circle{position:absolute;border-radius:50%}
.btn-solid{position:absolute;background:var(--teal);color:#fff;font-family:"Montserrat",sans-serif;font-weight:600;font-size:14px;letter-spacing:1px;text-align:center}
.btn-line{position:absolute;border:2px solid var(--teal);color:var(--teal);font-family:"Montserrat",sans-serif;font-weight:500;font-size:14px;letter-spacing:1px;text-align:center}

/* newsletter */
.updates{position:absolute;top:2157px;left:0;width:1200px;height:384px;background:linear-gradient(180deg,#3a6877 0%,#1c5365 45%,#134556 100%)}
.field{position:absolute;background:#fff;color:var(--muted);font-size:11px;padding-left:20px;letter-spacing:.5px}
.subscribe{position:absolute;background:var(--teal-btn);color:#fff;font-family:"Montserrat",sans-serif;font-weight:600;font-size:16px;letter-spacing:1.5px;text-align:center}

/* contact */
.contact{position:absolute;top:3076px;left:0;width:1200px;height:525px;background:var(--teal);overflow:hidden}
.contact-photo{position:absolute;left:560px;top:0;width:602px;height:525px;border-radius:0 262px 262px 0;background:linear-gradient(90deg,var(--teal) 0%,rgba(15,77,96,.6) 20%,#8a8f90 55%,#b5b2aa 100%)}
.cfield{position:absolute;border:1px solid rgba(255,255,255,.55);color:#e4eef1;font-size:12px;padding:12px 0 0 18px}

/* footer */
.foot-head{position:absolute;top:3662px;font-family:"Roboto",sans-serif;font-weight:500;font-size:15px;color:var(--teal);letter-spacing:.3px}
.foot-rule{position:absolute;top:3688px;width:52px;height:2px;background:var(--teal)}
.foot-list{position:absolute;top:3702px;list-style:none}
.foot-list li{font-size:13px;line-height:27px;color:var(--teal)}
.contact-row{position:absolute;left:848px;display:flex;align-items:flex-start;gap:14px;font-size:13px;color:var(--teal);line-height:18px}
.ico{width:26px;height:26px;border-radius:50%;background:var(--teal);flex:none;display:flex;align-items:center;justify-content:center}
.social{position:absolute;top:3836px;width:26px;height:26px;border-radius:50%;background:#c9cdd0}
.legal{position:absolute;top:3912px;left:0;width:1200px;height:75px;border-top:1px solid var(--rule);font-size:11.5px;color:var(--teal)}
</style>
</head>
<body>

<header class="site-header">
  <div class="brand"><span class="brand-dot"></span><span>ALVERON<br>REAL ESTATE</span></div>
  <nav class="nav">
    <a style="left:356px">ABOUT US ⌄</a>
    <a style="left:466px">OUR BUSINESSES ⌄</a>
    <a style="left:627px">INVESTORS LOBBY</a>
    <a style="left:793px">NEWS</a>
    <a style="left:880px">CONTACT US</a>
  </nav>
  <div class="login">LOG IN</div>
</header>

<section class="hero" role="img" aria-label="Aerial photo of a large warehouse under construction on cleared land">
  <div class="hero-shade"></div>
  <div class="play"><svg width="48" height="48" viewBox="0 0 48 48"><path d="M20 15 L33 24 L20 33 Z" fill="#fff"/></svg></div>
  <h1 class="hero-title">LEADING GLOBAL PRIVATE<br>EQUITY REAL ESTATE</h1>
  <div class="hero-btn">ABOUT US</div>
</section>

<section class="about">
  <div class="about-circle"></div>
  <div class="abs eyebrow" style="left:141px;top:84px;color:var(--teal)">Who we are</div>
  <h2 class="abs heading" style="left:140px;top:104px;font-size:31px;line-height:38px">About Alveron<br>Real Estate</h2>
  <div class="rule" style="left:141px;top:188px"></div>
  <p class="abs" style="left:551px;top:96px;width:525px;font-size:15.5px;line-height:28px">Lorem ipsum dolor sit amet, consectetur adipiscing elit, sed do eiusmod tempor incididunt ut labore et doloreUt enim ad minim veniam, quis nostrud exercitation ullamco laboris nisi ut aliquip ex ea Lorem ipsum dolor sit amet, consectetur adipiscing elit</p>
</section>

<section class="stats">
  <div class="stat" style="left:136px"><div class="value">$250</div><div class="label">Real estate projects</div></div>
  <div class="stat" style="left:410px"><div class="value">$25B</div><div class="label">Private equity</div></div>
  <div class="stat" style="left:664px"><div class="value">$13B</div><div class="label" style="margin-top:6px">Fund solutions</div></div>
  <div class="stat" style="left:920px"><div class="value" style="margin-top:22px">$10B</div><div class="label">Private equity</div></div>
</section>
<div class="vline" style="left:367px"></div>
<div class="vline" style="left:599px"></div>
<div class="vline" style="left:853px"></div>

<section class="platforms">
  <div class="abs eyebrow" style="left:0;top:1219px;width:1200px;text-align:center;color:var(--teal)">What we do</div>
  <h2 class="abs heading" style="left:0;top:1241px;width:1200px;text-align:center;font-size:28px">Our Investment Platforms</h2>
  <div class="rule" style="left:568px;top:1283px"></div>

  <div class="card" style="left:0;width:232px">
    <div class="card-photo" role="img" aria-label="Photo of a tablet displaying investment charts"></div>
    <div class="card-icon" style="left:91px;top:168px"><svg width="24" height="20" viewBox="0 0 24 20" fill="none" stroke="#fff" stroke-width="1.6"><rect x="1" y="1" width="22" height="14"/><path d="M4 12 L9 7 L13 10 L20 4"/><path d="M8 19 H16"/></svg></div>
    <div class="card-label" style="top:219px">Sed ut perspiciatis<br>unde omnis</div>
  </div>

  <div class="card card-feature" style="left:237px;width:240px">
    <div class="card-icon" style="left:95px;top:36px"><svg width="24" height="24" viewBox="0 0 24 24" fill="none" stroke="#fff" stroke-width="1.5"><rect x="3" y="3" width="18" height="14"/><circle cx="8" cy="20" r="2"/><circle cx="16" cy="20" r="2"/><path d="M7 8 H17 M7 12 H13"/></svg></div>
    <div class="card-label" style="top:100px">Sed ut perspiciatis<br>unde omnis</div>
    <div class="card-copy">Lorem ipsum dolor sit amet, consectetur adipiscing elit, sed do eiusmod tempor incididunt ut labore et</div>
    <div class="card-more">LEARN MORE</div>
  </div>

  <div class="card" style="left:481px;width:240px">
    <div class="card-photo" role="img" aria-label="Photo of a modern glass office building" style="background:linear-gradient(180deg,#b9bbbc,#55595c)"></div>
    <div class="card-icon" style="left:95px;top:172px"><svg width="24" height="24" viewBox="0 0 24 24" fill="none" stroke="#fff" stroke-width="1.5"><rect x="4" y="3" width="16" height="19"/><path d="M8 7h2M14 7h2M8 11h2M14 11h2M8 15h2M14 15h2M11 22v-4h2v4"/></svg></div>
    <div class="card-label" style="top:235px">Vatem quia voluptas<br>sit aspernatur</div>
  </div>

  <div class="card" style="left:726px;width:240px">
    <div class="card-photo" role="img" aria-label="Photo of a businessman facing a city skyline" style="background:linear-gradient(180deg,#7d8285,#3a3f42)"></div>
    <div class="card-icon" style="left:95px;top:172px"></div>
    <div class="card-label" style="top:235px">Sed ut perspiciatis<br>unde omnis</div>
  </div>

  <div class="card" style="left:969px;width:231px">
    <div class="card-photo" role="img" aria-label="Photo of a handshake in front of city towers" style="background:linear-gradient(180deg,#a9acae,#4a4e51)"></div>
    <div class="card-icon" style="left:90px;top:176px"><svg width="24" height="20" viewBox="0 0 24 20" fill="none" stroke="#fff" stroke-width="1.5"><path d="M2 8 L7 3 L12 6 L17 3 L22 8 L13 17 Z"/><path d="M9 11 L13 14"/></svg></div>
    <div class="card-label" style="top:237px">Nemo enim ipsam<br>voluptatem</div>
  </div>
</section>

<section class="edge">
  <h2 class="abs heading" style="left:144px;top:1717px;font-size:29px">Our Edge</h2>
  <div class="rule" style="left:145px;top:1757px"></div>
  <p class="abs" style="left:145px;top:1785px;width:455px">Lorem ipsum dolor sit amet, consectetur adipiscing elit, sed do eiusmod tempor incididunt ut co laboris nisi ut aliquip ex ea commodo consequat. Duis aute irure dolor in reprehende</p>
  <p class="abs" style="left:145px;top:1877px;width:455px">Aabor et dolore magna aliqua. Ut enim ad minim veniam, quis nostrud exercitation ullamco laboris nisi ut aliquip ex ea commodo consequat. Duis aute irure dolor in reprehenderitd exercitation</p>
  <div class="btn-solid" style="left:145px;top:1984px;width:273px;height:53px;line-height:53px">INVESTOR INFORMATION</div>
  <div class="photo-circle" role="img" aria-label="Black and white photo of glass skyscrapers seen from below" style="left:650px;top:1669px;width:418px;height:418px;background:linear-gradient(160deg,#d6d6d6,#7b7b7b 55%,#3b3b3b)"></div>
</section>

<section class="updates" role="img" aria-label="City skyline photo tinted in deep teal">
  <h2 class="abs heading" style="left:0;top:100px;width:1200px;text-align:center;color:#fff;font-size:30px">Stay Updated</h2>
  <div class="abs" style="left:0;top:153px;width:1200px;text-align:center;color:#fff;font-size:16px">Get our latest insights, firm announcements and Charitable Foundation updates.</div>
  <div class="field" style="left:201px;top:207px;width:305px;height:50px;line-height:50px">NAME*</div>
  <div class="field" style="left:516px;top:207px;width:305px;height:50px;line-height:50px">EMAIL*</div>
  <div class="subscribe" style="left:831px;top:206px;width:197px;height:51px;line-height:51px">SUBSCRIBE</div>
</section>

<section class="responsibility">
  <div class="photo-circle" role="img" aria-label="Black and white photo of colleagues working together at a desk" style="left:132px;top:2605px;width:418px;height:418px;background:linear-gradient(150deg,#cfcfcf,#8a8a8a 50%,#3f3f3f)"></div>
  <h2 class="abs heading" style="left:634px;top:2666px;font-size:27px">Our Responsibility</h2>
  <div class="rule" style="left:635px;top:2708px"></div>
  <p class="abs" style="left:636px;top:2729px;width:430px;font-size:13.5px;line-height:23px">Lorem ipsum dolor sit amet, consectetur adipiscing elit, sed do eiusmod tempor incididunt ut</p>
  <p class="abs" style="left:636px;top:2797px;width:430px;font-size:13.5px;line-height:23px">Aabor et dolore magna aliqua. Ut enim ad minim veniam, quis nostrud exercitation ullamco laboris nisi ut aliquip ex ea commodo consequat. Duis aute irure dolor in reprehenderitd exercitationna aliqua. Ut enim ad minim veniam.</p>
  <div class="btn-line" style="left:638px;top:2905px;width:167px;height:46px;line-height:42px">LEARN MORE</div>
</section>

<section class="contact">
  <div class="contact-photo" role="img" aria-label="Photo of three colleagues meeting around a laptop in a bright office"></div>
  <div class="abs eyebrow" style="left:121px;top:100px;color:#fff;font-size:14px">Contact us</div>
  <h2 class="abs heading" style="left:120px;top:120px;color:#fff;font-size:31px;font-weight:600">Get in Touch</h2>
  <div class="cfield" style="left:119px;top:179px;width:240px;height:42px">First Name</div>
  <div class="cfield" style="left:367px;top:179px;width:240px;height:42px">Last Name</div>
  <div class="cfield" style="left:119px;top:226px;width:240px;height:42px">Phone Number</div>
  <div class="cfield" style="left:367px;top:226px;width:240px;height:42px">Email address</div>
  <div class="cfield" style="left:119px;top:275px;width:488px;height:76px">Message</div>
  <div class="abs" style="left:119px;top:367px;width:208px;height:45px;border:2px solid #fff;color:#fff;font-family:'Montserrat',sans-serif;font-weight:600;font-size:13px;letter-spacing:1px;text-align:center;line-height:41px">SUBMIT MESSAGE</div>
</section>

<footer>
  <div class="foot-head" style="left:123px">IMPORTANT LINKS</div>
  <div class="foot-rule" style="left:124px"></div>
  <ul class="foot-list" style="left:124px"><li>About Us</li><li>Our Businesses</li><li>Investor Lobby</li><li>News</li><li>Contact Us</li></ul>

  <div class="foot-head" style="left:350px">EXPLORE ALVERON REAL ESTATE</div>
  <div class="foot-rule" style="left:350px"></div>
  <ul class="foot-list" style="left:352px"><li>Private Equity</li><li>Real Estate</li><li>Credit</li><li>Strategic Partners</li><li>Tactical Opportunities</li><li>Infrastructure</li></ul>
  <ul class="foot-list" style="left:555px"><li>Insurance Solutions</li><li>Life Sciences</li><li>Portfolio Operations</li><li>Technology and Innovations</li><li>Registered Products</li></ul>

  <div class="foot-head" style="left:843px">CONTACT DETAILS</div>
  <div class="foot-rule" style="left:844px"></div>
  <div class="contact-row" style="top:3704px"><span class="ico"><svg width="12" height="14" viewBox="0 0 12 14"><path d="M6 0a5 5 0 0 1 5 5c0 4-5 9-5 9S1 9 1 5a5 5 0 0 1 5-5z" fill="#fff"/><circle cx="6" cy="5" r="2" fill="#0f4d60"/></svg></span><span>240 N Harbor Way Unit B<br>Palm Grove, FL 33410</span></div>
  <div class="contact-row" style="top:3755px;align-items:center"><span class="ico"><svg width="12" height="12" viewBox="0 0 12 12"><path d="M2 0l2 3-1 1.5c.8 1.8 2.2 3.2 4 4L8.5 7.5l3 2-1 2.5C5 12 0 7 0 1z" fill="#fff"/></svg></span><span>555-014-2210</span></div>
  <div class="contact-row" style="top:3791px;align-items:center"><span class="ico"><svg width="13" height="10" viewBox="0 0 13 10"><rect x=".5" y=".5" width="12" height="9" fill="#fff"/><path d="M.5 .5l6 5 6-5" stroke="#0f4d60" fill="none"/></svg></span><span>info@alveronrealestate.com</span></div>
  <div class="social" style="left:854px;background:var(--teal)"></div>
  <div class="social" style="left:887px"></div>
  <div class="social" style="left:920px"></div>
  <div class="social" style="left:953px"></div>

  <div class="legal">
    <span class="abs" style="left:113px;top:25px">Copyright © 2022 Alveron Realestate</span>
    <span class="abs" style="left:830px;top:25px">Terms of Use &nbsp;|&nbsp; Sitemap &nbsp;|&nbsp; Privacy Policy</span>
  </div>
</footer>

</body>
</html>
```